I work in creative/artistic projects across different mediums.
It needs to communicate creativity, style, sexy, uniqueness, individuality and sophistication.
It should not look corporate.
Colours I like are black silver gold deep purple, chocolate, orchid.
It doesn't have to make use of all these colours.
I do not like bright primary colors.
Updates

Project Deadline Extended
Reason: Still in the communication process and to allow the person enough time to finish the design. Though i should know in the next day or two. Thank you.

Target Market(s)

creatives and companies wanting to inject creativity into thier business.

Industry/Entity Type

Work

Contact Information for Business Card

Corwin Haldley
0418592036
corwin@corwinhaldley-example.com

quietgoldenhourstudio.example.au

Requirements
Should not have
• Anything corporate OR OLD FASHIONED

```html
<!DOCTYPE html>
<html lang="en">
<head>
<meta charset="utf-8">
<title>Corwin Haldley – Business Card</title>
<link rel="stylesheet" href="https://fonts.googleapis.com/css2?family=Almendra:wght@400&family=Arimo:wght@400&display=swap">
<style>
  :root {
    --stage: #1b1119;
    --card-edge: #0d0710;
    --card-deep: #2a0c3b;
    --card-mid: #3a1650;
    --pattern-light: #4a2663;
    --name-panel: #4b2b66;
    --name-ink: #c9b8d8;
    --band: #43205b;
    --contact-ink: #cfc6d8;
    --icon-ink: #d6cfdd;
    --social-tile: #cbc3d3;
  }

  * { margin: 0; padding: 0; box-sizing: border-box; }

  html, body {
    width: 1200px;
    height: 800px;
    overflow: hidden;
    background: var(--stage);
  }

  .business-card {
    position: absolute;
    left: 150px;
    top: 140px;
    width: 900px;
    height: 520px;
    background: var(--card-deep);
    border: 8px solid var(--card-edge);
    overflow: hidden;
    font-family: "Arimo", Arial, sans-serif;
  }

  .circle-pattern-field {
    position: absolute;
    inset: 0;
    background:
      radial-gradient(ellipse at 55% 40%, var(--pattern-light) 0%, var(--card-mid) 45%, var(--card-deep) 100%);
    opacity: 0.85;
  }

  .name-panel {
    position: absolute;
    left: 400px;
    top: 58px;
    width: 330px;
    height: 56px;
    background: var(--name-panel);
    display: flex;
    align-items: center;
    justify-content: center;
  }

  .holder-name {
    font-family: "Almendra", Georgia, serif;
    font-size: 34px;
    font-weight: 400;
    color: var(--name-ink);
    letter-spacing: 1px;
  }

  .contact-list {
    position: absolute;
    left: 100px;
    top: 178px;
    list-style: none;
  }

  .contact-item {
    display: flex;
    align-items: center;
    height: 58px;
    color: var(--contact-ink);
    font-size: 21px;
    letter-spacing: 0.5px;
  }

  .contact-icon {
    width: 30px;
    height: 30px;
    margin-right: 28px;
    flex: none;
  }

  .contact-icon * {
    fill: none;
    stroke: var(--icon-ink);
    stroke-width: 1.8;
  }

  .accent-band {
    position: absolute;
    left: 0;
    right: 0;
    height: 10px;
    background: var(--band);
  }

  .accent-band--upper { top: 150px; left: 560px; }
  .accent-band--lower { top: 410px; }

  .social-mark {
    position: absolute;
    display: flex;
    align-items: center;
    gap: 10px;
    color: var(--contact-ink);
    font-size: 18px;
  }

  .social-tile {
    width: 40px;
    height: 40px;
    border-radius: 6px;
    background: var(--social-tile);
  }

  .social-mark--friendwall { left: 24px; bottom: 22px; }
  .social-mark--chirpline { right: 24px; top: 166px; flex-direction: row-reverse; }
</style>
</head>
<body>
  <section class="business-card">
    <div class="circle-pattern-field" role="img" aria-label="Grid of faint translucent purple circles across the card"></div>

    <div class="accent-band accent-band--upper"></div>
    <div class="accent-band accent-band--lower"></div>

    <div class="name-panel">
      <h1 class="holder-name">Corwin Haldley</h1>
    </div>

    <ul class="contact-list">
      <li class="contact-item">
        <svg class="contact-icon" viewBox="0 0 30 30" aria-hidden="true">
          <rect x="3" y="7" width="24" height="16"/>
          <polyline points="3,7 15,17 27,7"/>
        </svg>
        corwin@corwinhaldley-example.com
      </li>
      <li class="contact-item">
        <svg class="contact-icon" viewBox="0 0 30 30" aria-hidden="true">
          <rect x="9" y="3" width="12" height="24" rx="2"/>
          <line x1="13" y1="23.5" x2="17" y2="23.5"/>
        </svg>
        0418592036
      </li>
      <li class="contact-item">
        <svg class="contact-icon" viewBox="0 0 30 30" aria-hidden="true">
          <circle cx="15" cy="15" r="12"/>
          <ellipse cx="15" cy="15" rx="5" ry="12"/>
          <line x1="3" y1="15" x2="27" y2="15"/>
          <line x1="5" y1="9" x2="25" y2="9"/>
          <line x1="5" y1="21" x2="25" y2="21"/>
        </svg>
        quietgoldenhourstudio.example.au
      </li>
    </ul>

    <div class="social-mark social-mark--chirpline">
      <span class="social-tile"></span>
      <span class="social-name">Chirpline</span>
    </div>

    <div class="social-mark social-mark--friendwall">
      <span class="social-tile"></span>
      <span class="social-name">Friendwall</span>
    </div>
  </section>
</body>
</html>
```